Landing Page Design for Adult Dating Age Verification (18+)

The objective of this task is to design a visually appealing pre-landing page for the adult dating site "Quillmera (site: https://quillmera.com/)" with an age verification mechanism. The pre-landing page will feature two buttons that redirect visitors to the main offer. The design should also include a footer block that includes links to the terms of use, privacy policy, and contact us pages.

Design Requirements:
Develop an age verification section prominently displayed on the pre-landing page.
Design the section to include two buttons labeled "Yes" and "No" for visitors to confirm their age.
Ensure the section is visually appealing and clearly communicates the purpose of age verification.

Visual Appeal:
Create a visually appealing design that aligns with the branding and theme of the "Quillmera" adult dating site.
Use suitable color schemes, typography, and graphics to enhance the overall visual appeal of the pre-landing page.

Layout and Navigation:
Design an engaging and intuitive layout that encourages visitors to interact with the page and proceed to the main offer.
Ensure clear and visible navigation elements that direct visitors to the main offer or provide additional information.

Responsive Design:
Develop a responsive design that provides a seamless user experience across various devices, including desktop and mobile.
Ensure the design elements and layout adapt well to different screen sizes and resolutions.

File Formats and Assets:
Deliver the final design in PSD, AI, or Sketch format, ensuring that the files are well-organized and layered.
Include any necessary images or assets used in the design, ensuring they are of high quality and optimized for web use.

```html
<!DOCTYPE html>
<html lang="en">
<head>
<meta charset="utf-8">
<title>Quillmera – Age Verification</title>
<link rel="stylesheet" href="https://fonts.googleapis.com/css2?family=Oleo+Script:wght@400;700&family=IBM+Plex+Sans:wght@400;500&family=Lexend:wght@600&display=swap">
<style>
  :root {
    --ink: #252636;
    --white: #ffffff;
    --accent: #e444f2;
    --heart-line: #c24fd3;
    --heart-fill: rgba(255, 238, 244, 0.6);
    --brand-tint: #d5b3d9;
    --hero-top: #8a8f9c;
    --hero-mid: #c9b8b4;
    --hero-low: #3b3a44;
  }
  * { margin: 0; padding: 0; box-sizing: border-box; }
  html, body { width: 1200px; height: 1167px; overflow: hidden; }
  body { font-family: "IBM Plex Sans", sans-serif; background: var(--white); color: var(--ink); position: relative; }

  .site-header { position: absolute; top: 0; left: 0; width: 1200px; height: 99px; background: var(--white); }
  .brand { position: absolute; display: flex; align-items: center; gap: 10px; text-decoration: none;
           font-family: "IBM Plex Sans", sans-serif; font-weight: 500; }
  .brand-dot { border-radius: 50%; background: var(--brand-tint); flex: none; }
  .site-header .brand { left: 111px; top: 22px; font-size: 38px; color: var(--ink); }
  .site-header .brand-dot { width: 48px; height: 48px; }
  .menu-toggle { position: absolute; left: 999px; top: 37px; width: 23px; height: 18px; display: flex; flex-direction: column; justify-content: space-between; }
  .menu-toggle span { display: block; height: 3px; background: #000; }

  .hero { position: absolute; top: 99px; left: 0; width: 1200px; height: 672px; overflow: hidden; }
  .hero-photo { position: absolute; inset: 0;
    background: linear-gradient(160deg, var(--hero-low) 0%, var(--hero-top) 30%, var(--hero-mid) 55%, #d9d3d4 75%, var(--hero-low) 100%); }
  .age-gate { position: absolute; inset: 0; }
  .age-gate svg { position: absolute; left: 0; top: -99px; }
  .age-question { position: absolute; left: 0; width: 1200px; top: 246px; text-align: center;
    font-family: "Oleo Script", cursive; font-weight: 700; font-size: 51px; line-height: 64px; color: #0c0c0c; }
  .age-actions { position: absolute; top: 411px; left: 506px; display: flex; gap: 24px; }
  .age-btn { width: 89px; height: 36px; border-radius: 5px; display: flex; align-items: center; justify-content: center;
    font-family: "Lexend", sans-serif; font-weight: 600; font-size: 15px; text-decoration: none; }
  .age-btn--yes { background: var(--white); color: var(--accent); }
  .age-btn--no { background: var(--accent); color: var(--white); }

  .site-footer { position: absolute; top: 771px; left: 0; width: 1200px; height: 396px; background: var(--ink); color: var(--white); }
  .site-footer .brand { left: 0; width: 1200px; justify-content: center; top: 60px; font-size: 44px; color: var(--white); }
  .site-footer .brand-dot { width: 56px; height: 56px; }
  .footer-nav { position: absolute; top: 174px; width: 1200px; display: flex; justify-content: center; gap: 35px; }
  .footer-nav a { color: var(--white); text-decoration: none; font-size: 16.5px; }
  .copyright { position: absolute; top: 237px; width: 1200px; text-align: center; font-size: 14px; }
  .copyright a { color: var(--accent); }
  .social { position: absolute; top: 289px; left: 501px; display: flex; gap: 7.5px; }
  .social a { width: 44px; height: 44px; border-radius: 50%; background: var(--white); display: block; }
  .social a.is-active { background: var(--accent); }
</style>
</head>
<body>
  <header class="site-header">
    <a class="brand" href="https://quillmera.com/"><span class="brand-dot"></span>Quillmera</a>
    <div class="menu-toggle" aria-label="Menu"><span></span><span></span><span></span><span></span></div>
  </header>

  <main class="hero">
    <div class="hero-photo" role="img" aria-label="Photo of a couple embracing on white bed sheets"></div>
    <section class="age-gate">
      <svg width="1200" height="872" viewBox="0 0 1200 872" aria-hidden="true">
        <path d="M601 290 C560 220 470 195 400 215 C340 235 315 300 322 380 C330 470 420 560 601 701 C782 560 872 470 880 380 C887 300 862 235 802 215 C732 195 642 220 601 290 Z"
              fill="var(--heart-fill)" stroke="var(--heart-line)" stroke-width="5" stroke-linejoin="round"/>
      </svg>
      <h1 class="age-question">Are You over<br>18 Years Of Age?</h1>
      <div class="age-actions">
        <a class="age-btn age-btn--yes" href="https://quillmera.com/">Yes</a>
        <a class="age-btn age-btn--no" href="https://quillmera.com/">No</a>
      </div>
    </section>
  </main>

  <footer class="site-footer">
    <a class="brand" href="https://quillmera.com/"><span class="brand-dot"></span>Quillmera</a>
    <nav class="footer-nav">
      <a href="#">Terms Of Use</a>
      <a href="#">Privacy Policy</a>
      <a href="#">Contact Us</a>
    </nav>
    <p class="copyright">Copyright© 2023 &nbsp;<a href="https://quillmera.com/">Quillmera</a>&nbsp; | &nbsp;All Rights Reserved</p>
    <div class="social">
      <a class="is-active" href="#" aria-label="Social profile 1"></a>
      <a href="#" aria-label="Social profile 2"></a>
      <a href="#" aria-label="Social profile 3"></a>
      <a href="#" aria-label="Social profile 4"></a>
    </div>
  </footer>
</body>
</html>
```